Merrow Trade finance web design

We are a newly established business which provides invoice finance to Small Businesses in England and Wales.
Our approach is very much a funder where the small business owner can talk to the decision maker. We will guarantee on receipt of information, a decision within 24 hours.
We are not a bank so the look of the website need to be friendly but professional.
Have two types of people we are trying to attract to the website: 1) partners who are small business owners and 2) introducers who is accountants and commercial brokers who introduce us to the small businesses.
Currently no website, although domain has been reserved.
The design should be:
Professional
“Clean” Look
Designed to convey Trust and Authority.
Appeal to the small business owner.
Must incorporate:
Logo (attached)
Front page:Top tabs to other pages 1) About us 2) Services 3) Introducers 4) Contact us
Need picture and logo on page.
1) About us page- Room for talk about the company, the people and our critera.
2) Services page- We need for what invoice finance is, and 5 boxes for different services we will provide. (link on page to contact us)
3) Introducers page- We need a part for why become an introducer? Who we can help? Why we are different? (link on page to contact us)
4) Contact us page- Office address, email, tel and if possible a map and a contact me part which will email direct to us.
Text will be provided for the design, if we can see the setup of the website we will provide a part for each of the pages to support.
Styles we think convey the correct image:
www.dornelcapital.example
www.plivanlend.example
www.quorbacredit.example
Target Market(s)
Small business owners
Industry/Entity Type
Finance
Number of Pages Required
5+ page
Look and feel

```html
<!DOCTYPE html>
<html lang="en">
<head>
<meta charset="utf-8">
<title>Merrow Trade Finance</title>
<link rel="stylesheet" href="https://fonts.googleapis.com/css2?family=Roboto:wght@300;400;500;700&display=swap">
<style>
:root{
  --red:#e0353d;
  --red-dark:#c92a32;
  --ink:#2b2b2b;
  --dark:#333333;
  --grey-text:#8a8a8a;
  --body-text:#555555;
  --light-bg:#efefef;
  --white:#ffffff;
}
*{box-sizing:border-box;margin:0;padding:0}
html,body{width:1200px;height:3197px;overflow:hidden}
body{font-family:'Roboto',Arial,sans-serif;color:var(--ink);background:var(--white);position:relative}
.section{position:absolute;left:0;width:1200px}
.abs{position:absolute}
.accent{color:var(--red)}
.heading{font-size:40px;font-weight:400;letter-spacing:.5px;color:var(--ink);text-transform:uppercase;white-space:nowrap}

/* hero */
.hero{top:0;height:650px;overflow:hidden}
.hero-photo{position:absolute;inset:0;background:
  linear-gradient(180deg,rgba(255,255,255,.28) 0%,rgba(255,255,255,0) 45%,rgba(40,52,66,.25) 100%),
  linear-gradient(100deg,#6f7f8f 0%,#a8b4be 22%,#d9dfe4 45%,#c7ced4 62%,#8d99a4 82%,#5f6d7a 100%)}
.brand-hero{left:0;width:1200px;top:262px;text-align:center;font-size:78px;font-weight:700;color:var(--red);letter-spacing:1px;white-space:nowrap}
.call{left:0;width:1200px;top:414px;display:flex;justify-content:center;align-items:center;gap:18px;font-size:34px;color:#111}
.call-icon{width:76px;height:76px;border-radius:50%;background:rgba(255,255,255,.85);border:3px solid var(--red);display:flex;align-items:center;justify-content:center}

/* nav */
.nav{top:650px;height:62px;background:var(--red)}
.nav-list{position:absolute;left:77px;top:0;height:62px;display:flex;list-style:none}
.nav-list li{height:62px;display:flex;align-items:center;padding:0 26px;color:var(--white);font-size:15px;font-weight:400;text-transform:uppercase}
.nav-list li.active{background:var(--dark)}

/* welcome */
.welcome{top:712px;height:588px;background:var(--white)}
.welcome .heading{left:0;width:1200px;top:52px;text-align:center}
.welcome-intro{left:140px;width:920px;top:120px;text-align:center;font-size:14px;line-height:27px;color:var(--grey-text)}
.service-card{top:223px;width:250px;height:228px}
.service-img{width:250px;height:166px}
.service-label{height:62px;background:var(--red);color:var(--white);display:flex;align-items:center;justify-content:space-between;padding:0 14px;font-size:21px;text-transform:uppercase;white-space:nowrap}
.btn-dark{background:var(--dark);color:var(--white);font-size:20px;display:flex;align-items:center;justify-content:center;text-transform:uppercase}
.view-all{left:519px;top:468px;width:162px;height:56px}

/* about */
.about{top:1300px;height:415px;background:var(--light-bg)}
.about .heading{left:77px;top:58px}
.about-sub{left:79px;top:112px;font-size:18px;color:#333}
.about-text{left:79px;top:146px;width:680px;font-size:14px;line-height:29px;color:var(--body-text)}
.about-text p+p{margin-top:8px}
.know-more{left:77px;top:300px;width:177px;height:56px}
.brand-about{left:760px;top:170px;width:380px;text-align:center;font-size:40px;font-weight:700;color:var(--red);white-space:nowrap}

/* introducers */
.introducers{top:1715px;height:469px;background:var(--red)}
.intro-art{left:110px;top:70px;width:380px;height:350px;border-radius:26px;
  background:linear-gradient(150deg,#fafafa 0%,#e3e6ea 45%,#b8bfc6 100%)}
.introducers .heading{left:556px;top:56px;color:var(--ink)}
.introducers .heading .lite{color:var(--white)}
.intro-item{left:550px;width:570px;height:82px}
.intro-icon{position:absolute;left:0;top:0;width:80px;height:80px;border:3px solid var(--white);border-radius:50%;display:flex;align-items:center;justify-content:center;color:var(--white);font-size:46px;font-weight:700}
.intro-title{position:absolute;left:104px;top:2px;color:var(--white);font-size:18px;text-transform:uppercase}
.intro-desc{position:absolute;left:104px;top:30px;width:450px;color:#fde3e4;font-size:14px;line-height:23px}

/* news */
.news{top:2184px;height:471px;background:var(--white)}
.news .heading{left:0;width:1200px;top:54px;text-align:center}
.news-card{top:119px;width:250px}
.news-img{width:250px;height:164px}
.news-title{margin-top:28px;font-size:19px;text-transform:uppercase;color:var(--ink);white-space:nowrap}
.news-date{margin-top:8px;font-size:14px;font-style:italic;color:var(--red)}
.news-text{margin-top:10px;font-size:14px;line-height:24px;color:var(--grey-text)}

/* contact */
.contact{top:2655px;height:478px;background:var(--light-bg)}
.contact-map{left:380px;top:40px;width:560px;height:380px;background:#e6e6e6;border-radius:8px;opacity:.7}
.contact .heading{left:79px;top:60px}
.contact-text{left:79px;top:126px;width:520px;font-size:14px;line-height:26px;color:var(--body-text)}
.contact-line{left:77px;display:flex;gap:16px;font-size:14px;line-height:24px;color:var(--body-text)}
.contact-line svg{flex:none;margin-top:3px}
.contact-line .label{color:var(--red);font-weight:500}
.social{left:77px;top:402px;display:flex;gap:10px}
.social span{width:36px;height:36px;border-radius:50%;border:2px solid var(--red)}
.social span.filled{background:var(--red)}
.field{left:622px;width:501px;background:var(--white);border:1px solid #dcdcdc;font-size:14px;color:#9a9a9a;padding:16px 22px}
.submit{left:622px;top:362px;width:501px;height:52px}

/* footer */
.footer{top:3133px;height:64px;background:var(--red);display:flex;align-items:center;justify-content:center;color:var(--white);font-size:14px;gap:4px}
.footer strong{color:var(--ink);font-weight:700}
</style>
</head>
<body>

<header class="section hero">
  <div class="hero-photo" role="img" aria-label="Photo of a smiling business team gathered around a laptop in a bright office"></div>
  <div class="abs brand-hero">Merrow Trade Finance</div>
  <div class="abs call">
    <span>CALL US ON:</span>
    <span class="call-icon">
      <svg width="38" height="38" viewBox="0 0 24 24" fill="#e0353d"><path d="M6.6 10.8a15.1 15.1 0 0 0 6.6 6.6l2.2-2.2a1 1 0 0 1 1-.25 11.4 11.4 0 0 0 3.6.57 1 1 0 0 1 1 1V20a1 1 0 0 1-1 1A17 17 0 0 1 3 4a1 1 0 0 1 1-1h3.5a1 1 0 0 1 1 1c0 1.25.2 2.45.57 3.57a1 1 0 0 1-.25 1z"/></svg>
    </span>
    <span>123 456 7890</span>
  </div>
</header>

<nav class="section nav">
  <ul class="nav-list">
    <li class="active">Home</li>
    <li>About Us</li>
    <li>Services</li>
    <li>Introducers</li>
    <li>Contact Us</li>
  </ul>
</nav>

<section class="section welcome">
  <h1 class="abs heading">Welcome to <span class="accent">Merrow</span></h1>
  <p class="abs welcome-intro">It has survived not only five centuries. Lorem Ipsum is simply dummy text of the printing and typesetting industry. Lorem Ipsum has been the industry's standard dummy text ever since the 1500s, when an unknown printer took a galley of type and scrambled it to make a type specimen book. It has survived not only five centuries.</p>

  <div class="abs service-card" style="left:77px">
    <div class="service-img" role="img" aria-label="Image of a rising green bar chart over a grid" style="background:linear-gradient(170deg,#f3f5f2 0%,#d9e6d2 50%,#8fbf78 100%)"></div>
    <div class="service-label"><span>Services One</span><span>&#187;</span></div>
  </div>
  <div class="abs service-card" style="left:343px">
    <div class="service-img" role="img" aria-label="Image of business people standing beside financial charts" style="background:linear-gradient(170deg,#e4ecf3 0%,#a9bccd 50%,#667b90 100%)"></div>
    <div class="service-label"><span>Services Two</span><span>&#187;</span></div>
  </div>
  <div class="abs service-card" style="left:609px">
    <div class="service-img" role="img" aria-label="Image of a calculator and pen on a financial report" style="background:linear-gradient(170deg,#d3e1f0 0%,#7fa2cb 50%,#385a86 100%)"></div>
    <div class="service-label"><span>Services Three</span><span>&#187;</span></div>
  </div>
  <div class="abs service-card" style="left:875px">
    <div class="service-img" role="img" aria-label="Image of stacked gold coins" style="background:linear-gradient(170deg,#eff0ee 0%,#dccd9c 50%,#b08f3c 100%)"></div>
    <div class="service-label"><span>Services Four</span><span>&#187;</span></div>
  </div>

  <div class="abs btn-dark view-all">View All</div>
</section>

<section class="section about">
  <h2 class="abs heading">About <span class="accent">Merrow</span></h2>
  <div class="abs about-sub">Trade Finance Limited</div>
  <div class="abs about-text">
    <p>Lorem Ipsum is simply dummy text of the printing and typesetting industry. Lorem Ipsum has been the industry's standard dummy text ever since the 1500s, when an unknown printer took a galley of type and scrambled it to make a type specimen book.</p>
    <p>It has survived not only five centuries. Lorem Ipsum is simply dummy text of the printing and typesetting industry. Lorem Ipsum has been the industry's standard dummy text ever.</p>
  </div>
  <div class="abs btn-dark know-more">Know More</div>
  <div class="abs brand-about">Merrow Trade Finance</div>
</section>

<section class="section introducers">
  <div class="abs intro-art" role="img" aria-label="Illustration of a tablet showing a colourful bar chart and pie chart"></div>
  <h2 class="abs heading"><span>Our</span> <span class="lite">Introducers</span></h2>

  <div class="abs intro-item" style="top:126px">
    <div class="intro-icon">?</div>
    <div class="intro-title">Why become an introducer ?</div>
    <div class="intro-desc">Lorem Ipsum is simply dummy text of the printing and typesetting industry. Lorem Ipsum has been... &#187;</div>
  </div>
  <div class="abs intro-item" style="top:231px">
    <div class="intro-icon">?</div>
    <div class="intro-title">Who we help ?</div>
    <div class="intro-desc">Lorem Ipsum is simply dummy text of the printing and typesetting industry. Lorem Ipsum has been... &#187;</div>
  </div>
  <div class="abs intro-item" style="top:331px">
    <div class="intro-icon">?</div>
    <div class="intro-title">Why we are different ?</div>
    <div class="intro-desc">Lorem Ipsum is simply dummy text of the printing and typesetting industry. Lorem Ipsum has been... &#187;</div>
  </div>
</section>

<section class="section news">
  <h2 class="abs heading">Latest <span class="accent">News</span></h2>

  <article class="abs news-card" style="left:77px">
    <div class="news-img" role="img" aria-label="Photo of a businessman holding a tablet against a city skyline" style="background:linear-gradient(170deg,#c3d0dc 0%,#7a8fa4 50%,#3a4d61 100%)"></div>
    <div class="news-title">Lorem Ipsum Simple</div>
    <div class="news-date">13 Oct, 2016</div>
    <div class="news-text">Lorem Ipsum is simply dummy text of the printing and typesetting...</div>
  </article>
  <article class="abs news-card" style="left:343px">
    <div class="news-img" role="img" aria-label="Photo of a watering can watering a small money plant" style="background:linear-gradient(170deg,#f6f7f5 0%,#dfe4dc 50%,#a5b69b 100%)"></div>
    <div class="news-title">Lorem Ipsum Simple</div>
    <div class="news-date">13 Oct, 2016</div>
    <div class="news-text">Lorem Ipsum is simply dummy text of the printing and typesetting...</div>
  </article>
  <article class="abs news-card" style="left:609px">
    <div class="news-img" role="img" aria-label="Photo of colleagues meeting around a laptop" style="background:linear-gradient(170deg,#efedea 0%,#cdc7bf 50%,#8f8982 100%)"></div>
    <div class="news-title">Lorem Ipsum Simple</div>
    <div class="news-date">13 Oct, 2016</div>
    <div class="news-text">Lorem Ipsum is simply dummy text of the printing and typesetting...</div>
  </article>
  <article class="abs news-card" style="left:875px">
    <div class="news-img" role="img" aria-label="Photo of a businessman reviewing documents at a desk" style="background:linear-gradient(170deg,#eaf0f5 0%,#b3c3d2 50%,#50657b 100%)"></div>
    <div class="news-title">Lorem Ipsum Simple</div>
    <div class="news-date">13 Oct, 2016</div>
    <div class="news-text">Lorem Ipsum is simply dummy text of the printing and typesetting...</div>
  </article>
</section>

<section class="section contact">
  <div class="abs contact-map" role="img" aria-label="Faint world map behind the contact details"></div>
  <h2 class="abs heading">Contact <span class="accent">Us</span></h2>
  <p class="abs contact-text">Lorem Ipsum is simply dummy text of the printing and typesetting industry. Lorem Ipsum has been the industry's standard dummy text ever since the 1500s, when an unknown printer took a galley...</p>

  <div class="abs contact-line" style="top:226px">
    <svg width="22" height="20" viewBox="0 0 24 22" fill="none" stroke="#e0353d" stroke-width="2"><path d="M1 4l7-3 8 3 7-3v17l-7 3-8-3-7 3z"/><path d="M8 1v17M16 4v17"/></svg>
    <div><div class="label">Merrow Trade Finance Limited</div><div>101 - Lorem ipsum is simple dummy<br>text is printing and type text.</div></div>
  </div>
  <div class="abs contact-line" style="top:310px">
    <svg width="22" height="20" viewBox="0 0 24 24" fill="none" stroke="#e0353d" stroke-width="2"><path d="M6.6 10.8a15.1 15.1 0 0 0 6.6 6.6l2.2-2.2a1 1 0 0 1 1-.25 11.4 11.4 0 0 0 3.6.57 1 1 0 0 1 1 1V20a1 1 0 0 1-1 1A17 17 0 0 1 3 4a1 1 0 0 1 1-1h3.5a1 1 0 0 1 1 1c0 1.25.2 2.45.57 3.57a1 1 0 0 1-.25 1z"/></svg>
    <div>info@merrowtrade.example</div>
  </div>
  <div class="abs contact-line" style="top:348px">
    <svg width="22" height="18" viewBox="0 0 24 18" fill="none" stroke="#e0353d" stroke-width="2"><rect x="1" y="1" width="22" height="16"/><path d="M1 1l11 9 11-9"/></svg>
    <div>123 456 7890</div>
  </div>
  <div class="abs social" aria-label="Social links">
    <span class="filled"></span><span></span><span></span>
  </div>

  <div class="abs field" style="top:66px;height:50px">Name:</div>
  <div class="abs field" style="top:128px;height:50px">E-Mail:</div>
  <div class="abs field" style="top:189px;height:50px">Subject:</div>
  <div class="abs field" style="top:250px;height:100px">Message</div>
  <div class="abs btn-dark submit">Submit</div>
</section>

<footer class="section footer"><strong>MERROW</strong> - 2016 All rights reserved.</footer>

</body>
</html>
```